KRV Photography Business Card Design

I would like a business card designed in the shape of a camera.
Would like to see various camera designs. Would like to see what the card looks like in different colors. Would like to see which logo looks better on the various camera designs so please show me some with the white logo and some with the black logo. If you need a different file formats please let me know.
Project Deadline Extended Reason: My grandfather passed away and dealing with funeral plans so need to extend deadline. Added Tuesday, March 1, 2016
Project Deadline Extended
Reason: I just got back from out of town. My grandfather's passing was the primary focus for me these past few weeks and the funeral is over so now I will concentrate on picking my business card design. I really appreciate each designer who has taken the time to submit a design. Your effort has not gone unnoticed. I look forward to seeing more amazing designs.
Business
Contact Information for Business Card
Dorine
555-418-2706
https://www.facebook.com/krvphotographyfreelance/
MonaDorine@krv-photography.example

```html
<!DOCTYPE html>
<html lang="en">
<head>
<meta charset="utf-8">
<title>KRV Photography — Business Cards</title>
<link rel="stylesheet" href="https://fonts.googleapis.com/css2?family=Open+Sans:wght@400;600;700&display=swap">
<style>
  :root {
    --backdrop: #bcbdbf;
    --card: #000000;
    --accent: #d38a2c;
    --gold: #caa24c;
    --gold-light: #f2d98a;
    --white: #ffffff;
  }
  * { box-sizing: border-box; margin: 0; padding: 0; }
  html, body { width: 1200px; height: 927px; overflow: hidden; }
  body {
    position: relative;
    background: var(--backdrop);
    font-family: "Open Sans", Arial, sans-serif;
  }
  .camera-card {
    position: absolute;
    top: 310px;
    width: 546px;
    height: 328px;
    filter: drop-shadow(6px 8px 8px rgba(0,0,0,0.35));
  }
  .camera-card--orange { left: 39px; }
  .camera-card--white { left: 615px; }
  .camera-body {
    position: absolute;
    inset: 0;
    background: var(--card);
    border-radius: 20px;
  }
  .shutter-button {
    position: absolute;
    left: 72px;
    top: -6px;
    width: 64px;
    height: 12px;
    background: var(--card);
    border-radius: 6px 6px 0 0;
  }
  .viewfinder {
    position: absolute;
    left: 385px;
    top: -21px;
    width: 104px;
    height: 30px;
    background: var(--card);
    border-radius: 10px 10px 0 0;
  }
  .contact {
    position: absolute;
    left: 21px;
    top: 16px;
  }
  .contact__name {
    font-size: 22px;
    font-weight: 700;
    letter-spacing: 1.6px;
    line-height: 1.2;
  }
  .contact__list {
    list-style: none;
    margin-top: 10px;
    font-size: 13px;
    letter-spacing: 0.9px;
    line-height: 16px;
  }
  .contact__item {
    display: flex;
    align-items: center;
    gap: 11px;
  }
  .contact__icon { width: 11px; height: 11px; flex: none; }
  .camera-card--orange .contact { color: var(--accent); }
  .camera-card--white .contact { color: var(--white); }
  .brand {
    position: absolute;
    right: 23px;
    top: 200px;
    width: 230px;
    text-align: right;
  }
  .brand__dot {
    position: absolute;
    left: 75px;
    top: 0;
    width: 74px;
    height: 74px;
    border-radius: 50%;
    background: radial-gradient(circle at 40% 35%, var(--gold-light), var(--gold) 70%);
  }
  .brand__name {
    position: absolute;
    right: 0;
    top: 92px;
    font-size: 21px;
    font-weight: 400;
    letter-spacing: 0.6px;
    color: var(--gold);
    white-space: nowrap;
  }
</style>
</head>
<body>

<div class="camera-card camera-card--orange">
  <div class="shutter-button"></div>
  <div class="viewfinder"></div>
  <div class="camera-body">
    <div class="contact">
      <p class="contact__name">THEO VARNELL</p>
      <ul class="contact__list">
        <li class="contact__item">
          <svg class="contact__icon" viewBox="0 0 12 12"><path d="M2.5 1 L4.5 1 L5 3.5 L3.8 4.5 Q4.8 6.8 7.5 8.2 L8.5 7 L11 7.5 L11 9.5 Q10.5 11 9 11 Q2 10 1 3 Q1 1.5 2.5 1 Z" fill="currentColor"/></svg>
          <span>+330 5550-1942</span>
        </li>
        <li class="contact__item">
          <svg class="contact__icon" viewBox="0 0 12 12"><rect x="1" y="2.5" width="10" height="7" fill="none" stroke="currentColor" stroke-width="1.2"/><path d="M1 2.5 L6 6.5 L11 2.5" fill="none" stroke="currentColor" stroke-width="1.2"/></svg>
          <span>theo@varnellmail.example</span>
        </li>
      </ul>
    </div>
    <div class="brand">
      <span class="brand__dot"></span>
      <p class="brand__name">KRV PHOTOGRAPHY</p>
    </div>
  </div>
</div>

<div class="camera-card camera-card--white">
  <div class="shutter-button"></div>
  <div class="viewfinder"></div>
  <div class="camera-body">
    <div class="contact">
      <p class="contact__name">THEO VARNELL</p>
      <ul class="contact__list">
        <li class="contact__item">
          <svg class="contact__icon" viewBox="0 0 12 12"><path d="M2.5 1 L4.5 1 L5 3.5 L3.8 4.5 Q4.8 6.8 7.5 8.2 L8.5 7 L11 7.5 L11 9.5 Q10.5 11 9 11 Q2 10 1 3 Q1 1.5 2.5 1 Z" fill="currentColor"/></svg>
          <span>+330 5550-1942</span>
        </li>
        <li class="contact__item">
          <svg class="contact__icon" viewBox="0 0 12 12"><rect x="1" y="2.5" width="10" height="7" fill="none" stroke="currentColor" stroke-width="1.2"/><path d="M1 2.5 L6 6.5 L11 2.5" fill="none" stroke="currentColor" stroke-width="1.2"/></svg>
          <span>theo@varnellmail.example</span>
        </li>
      </ul>
    </div>
    <div class="brand">
      <span class="brand__dot"></span>
      <p class="brand__name">KRV PHOTOGRAPHY</p>
    </div>
  </div>
</div>

</body>
</html>
```